Calderwick Air Business Card Design

Design new, 2 sides, business cards for a residential and light commercial heating, air conditioning contractor.

Target Market(s)

Homeowners, small businesses

Industry/Entity Type

Business

Contact Information for Business Card

Dominic Westerhall
Phone - 862-415-2736
Email
Address - PO box 518
Brightwater NJ 07912
Website - www.HarborBreezeLLC.example

Requirements
Must have
• logo, company colors, standard size with no die cut, so I can use nova stamp

```html
<!DOCTYPE html>
<html lang="en">
<head>
<meta charset="utf-8">
<title>Calderwick Air – Business Card</title>
<link rel="stylesheet" href="https://fonts.googleapis.com/css2?family=Arimo:wght@400;700&display=swap">
<style>
  :root {
    --backdrop: #3b3431;
    --card: #141414;
    --card-edge: #1d1d1d;
    --brand-red: #c23848;
    --brand-orange: #e39a3f;
    --text-light: #e6e6e6;
    --text-soft: #bdbdbd;
    --rule: #d9d9d9;
  }
  * { margin: 0; padding: 0; box-sizing: border-box; }
  html, body {
    width: 1200px;
    height: 864px;
    overflow: hidden;
    background: var(--backdrop);
    font-family: "Arimo", Arial, sans-serif;
  }
  .stage {
    position: relative;
    width: 1200px;
    height: 864px;
  }
  .card {
    position: absolute;
    top: 284px;
    width: 520px;
    height: 297px;
    background: var(--card);
    border: 1px solid var(--card-edge);
    border-radius: 3px;
    box-shadow: 0 10px 24px rgba(0,0,0,0.35);
    overflow: hidden;
  }
  .card--front { left: 50px; }
  .card--back { left: 630px; }

  .wordmark {
    font-weight: 700;
    color: var(--brand-orange);
    letter-spacing: 1px;
    text-transform: uppercase;
    display: flex;
    align-items: center;
    gap: 10px;
    white-space: nowrap;
  }
  .wordmark__dot {
    width: 14px;
    height: 14px;
    border-radius: 50%;
    background: var(--brand-red);
    flex: none;
  }
  .card--front .wordmark {
    position: absolute;
    left: 0; right: 0; top: 0; bottom: 0;
    justify-content: center;
    font-size: 34px;
  }
  .card--back .wordmark {
    position: absolute;
    right: 30px;
    top: 110px;
    font-size: 22px;
    line-height: 26px;
  }
  .card--back .wordmark__dot { width: 11px; height: 11px; }

  .person {
    position: absolute;
    left: 30px;
    top: 36px;
  }
  .person__name {
    color: var(--brand-red);
    font-size: 17px;
    line-height: 20px;
  }
  .person__title {
    color: var(--brand-orange);
    font-size: 13px;
    line-height: 16px;
  }
  .rule {
    position: absolute;
    height: 1px;
    background: var(--rule);
  }
  .rule--top { left: 30px; top: 84px; width: 240px; }
  .rule--bottom { left: 260px; right: 30px; top: 190px; }

  .contact-list {
    position: absolute;
    left: 30px;
    top: 96px;
    list-style: none;
  }
  .contact-list li {
    display: flex;
    align-items: center;
    gap: 9px;
    color: var(--text-light);
    font-size: 12px;
    line-height: 19px;
  }
  .contact-list svg { width: 11px; height: 11px; fill: var(--brand-red); flex: none; }

  .address {
    position: absolute;
    right: 30px;
    top: 204px;
    text-align: right;
    color: var(--text-light);
    font-size: 12px;
    line-height: 21px;
    font-style: normal;
  }
  .address__web { letter-spacing: 1.5px; color: var(--text-soft); }
</style>
</head>
<body>
<main class="stage">
  <section class="card card--front" aria-label="Card front">
    <div class="wordmark"><span class="wordmark__dot"></span>Calderwick Air</div>
  </section>

  <section class="card card--back" aria-label="Card back">
    <div class="person">
      <p class="person__name">Dominic Westerhall</p>
      <p class="person__title">President</p>
    </div>
    <div class="rule rule--top"></div>

    <ul class="contact-list">
      <li>
        <svg viewBox="0 0 12 12"><path d="M2 1h3l1 3-1.5 1a6 6 0 0 0 2.5 2.5L8 6l3 1v3c0 .6-.4 1-1 1A9 9 0 0 1 1 2c0-.6.4-1 1-1z"/></svg>
        862 415 2736
      </li>
      <li>
        <svg viewBox="0 0 12 12"><path d="M3.5 0h5a1 1 0 0 1 1 1v10a1 1 0 0 1-1 1h-5a1 1 0 0 1-1-1V1a1 1 0 0 1 1-1zm.5 1.5v7.5h4V1.5z"/></svg>
        862 415 2790
      </li>
      <li>
        <svg viewBox="0 0 12 12"><path d="M3 0h6v3H3zM1 4h10a1 1 0 0 1 1 1v4H9.5v3h-7V9H0V5a1 1 0 0 1 1-1zm2.5 4v3h5V8z"/></svg>
        862 415 2791
      </li>
      <li>
        <svg viewBox="0 0 12 12"><path d="M0 2h12v1L6 7 0 3zM0 4.2l6 4 6-4V10H0z"/></svg>
        dominic@calderwickair.example
      </li>
    </ul>

    <div class="wordmark"><span class="wordmark__dot"></span>Calderwick Air</div>
    <div class="rule rule--bottom"></div>

    <address class="address">
      <p>PO box 518</p>
      <p>Brightwater NJ 07912</p>
      <p class="address__web">www.CalderwickAirLLC.example</p>
    </address>
  </section>
</main>
</body>
</html>
```